Business Card & Email Signature Design || Upmarket + Luxury

Rima Vale Honey, a New Zealand Manuka Honey company needs a Business Card & Email Signature design.

Our logo's are attached in Gold & Black versions, feel free to be creative with how you use the logo and it's patterns in your design.

Style:
- Looking for an Elegant, Luxurious, Upmarket feel.
- Black/Matte Black Card, Gold Foil, UV Embossing

Information to Add:

- Logo
- Company Name: Rima Vale Honey
- Name: Martin Holloway
- Title: Creative Director
- Phone: +64 2815 96 417
- Email: martin@rimavalehoney.example.nz
- Website: www.rimavalehoney.example.nz

- Socials: ***For email Signature Only***
- Facebook: https://www.facebook.com/rimavalehoney/
- Instagram: https://www.instagram.com/rimavalehoney/

Target Market(s)

Asia/Europe Luxury, Upmarket

Contact Information for Business Card

- Logo
- Name: Martin Holloway
- Phone: +64 2815 96 417

Font styles to use
Other font styles liked:
• Champagne & Limousines (Attached)

Requirements
Must have
• Business Card & Email Signature Design.

Looking for a Sleek, Luxury, Upmarket Design.

```html
<!DOCTYPE html>
<html lang="en">
<head>
<meta charset="utf-8">
<title>Rima Vale Honey Co. – Business Card</title>
<link rel="stylesheet" href="https://fonts.googleapis.com/css2?family=Montserrat:wght@300;400&family=Oswald:wght@600&display=swap">
<style>
  :root {
    --backdrop: #aeafaa;
    --card: #1e1e1e;
    --card-edge: #b9b865;
    --gold: #c9a75e;
    --gold-light: #ecd08a;
    --gold-dark: #9a7431;
  }
  * { margin: 0; padding: 0; box-sizing: border-box; }
  html, body {
    width: 1200px; height: 801px; overflow: hidden;
    background: var(--backdrop);
  }
  .canvas {
    width: 1200px; height: 801px;
    display: flex; align-items: center; justify-content: center; gap: 40px;
  }
  .card {
    width: 540px; height: 309px;
    background: var(--card);
    border-bottom: 3px solid var(--card-edge);
    box-shadow: 0 10px 24px rgba(0,0,0,0.28);
    position: relative;
    color: var(--gold);
    font-family: "Montserrat", sans-serif;
  }

  /* Front */
  .card--front { display: flex; flex-direction: column; align-items: center; }
  .wordmark {
    margin-top: 78px;
    font-weight: 300; font-size: 25px; letter-spacing: 6px;
    color: var(--gold-light);
  }
  .details {
    margin-top: 62px;
    display: flex; align-items: center; gap: 18px;
  }
  .person { text-align: right; }
  .person__name {
    font-family: "Oswald", sans-serif; font-weight: 600;
    font-size: 27px; letter-spacing: 0.5px; line-height: 1;
    background: linear-gradient(180deg, var(--gold-light), var(--gold-dark));
    -webkit-background-clip: text; background-clip: text; color: transparent;
  }
  .person__title { font-weight: 300; font-size: 13px; letter-spacing: 1px; margin-top: 6px; }
  .divider { width: 1px; height: 52px; background: var(--gold); }
  .contacts { list-style: none; font-size: 11.5px; font-weight: 400; line-height: 1.65; }
  .contacts li { display: flex; align-items: center; gap: 6px; }
  .contacts svg { width: 10px; height: 10px; flex: none; }

  /* Back */
  .card--back { display: flex; flex-direction: column; align-items: center; justify-content: center; }
  .seal {
    width: 196px; height: 196px; border-radius: 50%;
    border: 1.5px solid var(--gold);
    display: flex; align-items: center; justify-content: center;
    text-align: center;
  }
  .seal__name {
    font-weight: 300; font-size: 17px; letter-spacing: 4px; line-height: 1.6;
    color: var(--gold-light);
  }
  .tagline {
    margin-top: 16px;
    font-weight: 400; font-size: 10px; letter-spacing: 3px;
  }
</style>
</head>
<body>
<main class="canvas">
  <section class="card card--front" aria-label="Business card front">
    <p class="wordmark">RIMA VALE HONEY CO.</p>
    <div class="details">
      <div class="person">
        <p class="person__name">MARTIN HOLLOWAY</p>
        <p class="person__title">Creative Director</p>
      </div>
      <span class="divider"></span>
      <ul class="contacts">
        <li>
          <svg viewBox="0 0 10 10" aria-hidden="true"><path d="M2 1 L4 3 L3 4 Q4 6 6 7 L7 6 L9 8 L8 9 Q3 9 1 2 Z" fill="currentColor"/></svg>
          +64 2815 96 417
        </li>
        <li>
          <svg viewBox="0 0 10 10" aria-hidden="true"><rect x="0.7" y="2" width="8.6" height="6" fill="none" stroke="currentColor" stroke-width="1"/><path d="M0.7 2 L5 5.5 L9.3 2" fill="none" stroke="currentColor" stroke-width="1"/></svg>
          martin@rimavalehoney.example.nz
        </li>
        <li>
          <svg viewBox="0 0 10 10" aria-hidden="true"><circle cx="5" cy="5" r="4.2" fill="none" stroke="currentColor" stroke-width="1"/><ellipse cx="5" cy="5" rx="1.8" ry="4.2" fill="none" stroke="currentColor" stroke-width="0.8"/><path d="M0.8 5 H9.2" stroke="currentColor" stroke-width="0.8"/></svg>
          www.rimavalehoney.example.nz
        </li>
      </ul>
    </div>
  </section>

  <section class="card card--back" aria-label="Business card back">
    <div class="seal">
      <p class="seal__name">RIMA VALE<br>HONEY CO.</p>
    </div>
    <p class="tagline">GATHERED IN QUIET VALLEYS</p>
  </section>
</main>
</body>
</html>
```